Onboarding Infographic/brochure

We are a small criminal defense firm looking to create some sort of infographic or brochure that we can onboard new clients with. We are currently sending it out via email but want something a bit cooler and fun to send to clients. The information is:

A Few Quick Rules

We are here to help each step of the way. While questions are never discouraged, this letter will answer some of the most common ones we get asked.

Communications

As a client, you should always be in the loop. While we will try to respond to questions as quickly as possible, sometimes we are unable to respond right away. Do not worry - we promise to get back to you soon. Some questions might take some time to research, and a correct answer is better than a quick one.

Appointments

One of the benefits of having an attorney is the ability to discuss your case outside of court, minus the stress and headaches. If you need an appointment, please contact the office.

Appointments must be scheduled in advance. We do not want you to make a special trip to the office only to learn that we are in court or otherwise unavailable.

Jail Visits

If your family member is currently in jail, we take that very seriously. We will visit your loved one and introduce ourselves. While the case is ongoing, we ask that a family member be designated a “contact” person so that messages can be relayed quickly. Never discuss the facts of the case over the phone with someone who is in jail. Jail calls are recorded and we have seen too many cases go south based on remarks made over recorded lines.

Police Reports and Discovery

We will do our best to provide you with copies of everything we receive on your case. Most information will be emailed, so please keep your email address up to date.

Changes in Contact Information

If you move or change numbers during the case, please let us know. It is difficult to help if we are unable to reach you, and helping you is why we are here.

Court Appearances

Cases do not get resolved as quickly as they do on television. Expect there to be several hearings in your case and it may be necessary for you to attend one or more of them. If a hearing is set, you will receive notice of the date and time of each hearing.

Billing and Collections

We understand that this investment was a huge decision for you. As we focus on providing the best representation, we will need for you to stay on schedule with any payment arrangements agreed to at the time of your initial consultation.

Again, thank you for your trust in us. We look forward to getting a fantastic outcome on your case.

Target Market(s)

Criminal defense clients and their families

Industry/Entity Type

Legal

Font styles to use
Serif

Requirements
Must have
• Must incorporate all of the rules we email out. Would like diagrams, images or pictures
Nice to have
• We attached a Welcome brochure. Not sure I want it to look super similar, hence the request for infographic.

```html
<!DOCTYPE html>
<html lang="en">
<head>
<meta charset="UTF-8">
<title>A Few Quick Rules – Client Onboarding</title>
<link rel="stylesheet" href="https://fonts.googleapis.com/css2?family=Montserrat:wght@400;500;700&display=swap">
<style>
  :root {
    --brand-blue: #0b2ff0;
    --icon-tint-a: rgba(11, 47, 240, 0.22);
    --icon-tint-b: rgba(11, 47, 240, 0.08);
    --ink: #2b2f3a;
    --ink-dark: #0d0f14;
    --bg-start: #f8fdfd;
    --bg-end: #c9fbf5;
    --rule: 2px;
  }
  * { margin: 0; padding: 0; box-sizing: border-box; }
  html, body { width: 753px; height: 1200px; overflow: hidden; }
  body {
    font-family: "Montserrat", sans-serif;
    color: var(--ink);
    background: linear-gradient(100deg, var(--bg-start) 0%, #e4fcfb 55%, var(--bg-end) 100%);
  }
  .sheet { position: relative; width: 753px; height: 1200px; }

  .page-title {
    position: absolute; left: 47px; top: 42px;
    font-size: 17px; font-weight: 700; color: var(--brand-blue);
    letter-spacing: 0.2px;
  }
  .intro {
    position: absolute; left: 47px; top: 73px;
    font-size: 12.8px; line-height: 19px; white-space: nowrap;
  }

  .rule { position: absolute; height: var(--rule); background: var(--brand-blue); }
  .rule--full { left: 47px; width: 659px; }
  .rule--right { left: 379px; width: 327px; }
  .divider {
    position: absolute; left: 378px; top: 126px; width: var(--rule); height: 953px;
    background: var(--brand-blue);
  }

  .topic { position: absolute; }
  .topic--left { left: 47px; }
  .topic--right { left: 399px; }
  .topic-icon {
    display: block; width: 52px; height: 52px; border-radius: 6px;
    background: linear-gradient(135deg, var(--icon-tint-a), var(--icon-tint-b));
  }
  .topic-icon--wide { width: 75px; }
  .topic-icon--card { width: 58px; }
  .topic-icon--bill { width: 59px; }
  .topic-title {
    margin-top: 13px;
    font-size: 17px; font-weight: 700; color: var(--brand-blue); white-space: nowrap;
  }
  .topic-body {
    margin-top: 8px;
    font-size: 12.8px; line-height: 19px; white-space: nowrap;
  }
  .topic-body + .topic-body { margin-top: 19px; }

  .closing {
    position: absolute; left: 47px; top: 1094px;
    font-size: 12.8px; white-space: nowrap;
  }
  .site-url {
    position: absolute; left: 47px; top: 1140px;
    font-size: 12px; font-weight: 700; color: var(--brand-blue); letter-spacing: 0.1px;
  }
  .firm-name {
    position: absolute; right: 47px; top: 1139px;
    font-size: 12.5px; font-weight: 700; color: var(--ink-dark);
  }
</style>
</head>
<body>
<main class="sheet">
  <h1 class="page-title">A FEW QUICK RULES</h1>
  <p class="intro">We are here to help each step of the way. While questions are never discouraged, this letter will answer<br>some of the most common ones we get asked.</p>

  <div class="rule rule--full" style="top:125px"></div>
  <div class="divider"></div>
  <div class="rule rule--full" style="top:425px"></div>
  <div class="rule rule--right" style="top:630px"></div>
  <div class="rule rule--full" style="top:834px"></div>
  <div class="rule rule--full" style="top:1077px"></div>

  <section class="topic topic--left" style="top:146px">
    <div class="topic-icon topic-icon--wide" role="img" aria-label="Line icon of two speech bubbles"></div>
    <h2 class="topic-title">Communications</h2>
    <p class="topic-body">As a client, you should always be in the loop.<br>While we will try to respond to questions as<br>quickly as possible, sometimes we are unable<br>to respond right away.<br>Do not worry - we promise to get back to you<br>soon. Some questions might take some time to<br>research, and a correct answer is better than a<br>quick one.</p>
  </section>

  <section class="topic topic--right" style="top:146px">
    <div class="topic-icon" role="img" aria-label="Line icon of a calendar with a clock"></div>
    <h2 class="topic-title">Appointments</h2>
    <p class="topic-body">One of the benefits of having an attorney is the<br>ability to discuss your case outside of court,<br>minus the stress and headaches. If you need an<br>appointment, please contact the office.</p>
    <p class="topic-body">Appointments must be scheduled in advance.<br>We do not want you to make a special trip to the<br>office only to learn that we are in court or<br>otherwise unavailable.</p>
  </section>

  <section class="topic topic--left" style="top:445px">
    <div class="topic-icon" role="img" aria-label="Line icon of a jail visiting booth"></div>
    <h2 class="topic-title">Jail Visits</h2>
    <p class="topic-body">If your family member is currently in jail, we take<br>that very seriously. We will visit your loved one<br>and introduce ourselves. While the case is<br>ongoing, we ask that a family member be<br>designated a “contact” person so that messages<br>can be relayed quickly.</p>
    <p class="topic-body">Never discuss the facts of the case over the phone<br>with someone who is in jail. Jail calls are recorded<br>and we have seen too many cases go south<br>based on remarks made over recorded lines.</p>
  </section>

  <section class="topic topic--right" style="top:445px">
    <div class="topic-icon" role="img" aria-label="Line icon of a police report file"></div>
    <h2 class="topic-title">Police Reports and Discovery</h2>
    <p class="topic-body">We will do our best to provide you with copies<br>of everything we receive on your case. Most<br>information will be emailed, so please keep<br>your email address up to date.</p>
  </section>

  <section class="topic topic--right" style="top:650px">
    <div class="topic-icon topic-icon--card" role="img" aria-label="Line icon of a contact card"></div>
    <h2 class="topic-title">Changes in Contact Information</h2>
    <p class="topic-body">If you move or change numbers during the case,<br>please let us know. It is difficult to help if we are<br>unable to reach you, and helping you is why we<br>are here.</p>
  </section>

  <section class="topic topic--left" style="top:855px">
    <div class="topic-icon" role="img" aria-label="Line icon of a courthouse"></div>
    <h2 class="topic-title">Court Appearances</h2>
    <p class="topic-body">Cases do not get resolved as quickly as they do<br>on television. Expect there to be several hearings<br>in your case and it may be necessary for you to<br>attend one or more of them. If a hearing is set,<br>you will receive notice of the date and time of<br>each hearing.</p>
  </section>

  <section class="topic topic--right" style="top:855px">
    <div class="topic-icon topic-icon--bill" role="img" aria-label="Line icon of an invoice with a coin"></div>
    <h2 class="topic-title">Billing and Collections</h2>
    <p class="topic-body">We understand that this investment was a huge<br>decision for you. As we focus on providing the<br>best representation, we will need for you to stay<br>on schedule with any payment arrangements<br>agreed to at the time of your initial consultation.</p>
  </section>

  <p class="closing">Again, thank you for your trust in us. We look forward to getting a fantastic outcome on your case.</p>

  <footer>
    <p class="site-url">WWW.VERITASDEFENSEPARTNERS.COM</p>
    <p class="firm-name">VERITAS DEFENSE PARTNERS</p>
  </footer>
</main>
</body>
</html>
```